Velk Partners Building Business Cards

We need a business card that reflects our business as "Solar Experts" in San Diego. Browse our website www.velkpartners.example our License needs to be displayed as "CSLB# 3867140" our phone number is (619) 555-0187

Save thousands on your electric bills and increase the value of your home while helping to protect the environment. Our solar installation experts will help you design the system that's right for you, using only the highest quality equipment that will look great and give you ideal performance. Our goal is to make you energy independent, and get your electric bill to 0.

Paul Osterby
(619) 555-0187
paul@velkpartners.example

Target Market(s)

Home owners in san diego looking for solar

Industry/Entity Type

Solar Energy

Contact Information for Business Card

Paul Osterby
(619) 555-0187
paul@velkpartners.example

Font styles to use
Other font styles liked:
• Use our logo font

Requirements
Must have
• License needs to be displayed as "CSLB# 3867140" our phone number is (619) 555-0187
Nice to have
• Real images of rooftop home solar in san diego
Should not have
• our business address

```html
<!DOCTYPE html>
<html lang="en">
<head>
<meta charset="utf-8">
<title>Velk Partners Building – Business Card</title>
<link rel="stylesheet" href="https://fonts.googleapis.com/css2?family=Open+Sans:ital,wght@0,400;0,700;1,400&display=swap">
<style>
  :root {
    --backdrop: #4d4d4f;
    --card-white: #ffffff;
    --navy: #1b3b72;
    --sun: #fbb222;
    --sun-deep: #f8aa00;
    --ink-light: #ffffff;
  }
  * { box-sizing: border-box; margin: 0; padding: 0; }
  html, body {
    width: 1105px;
    height: 1200px;
    overflow: hidden;
  }
  body {
    background: var(--backdrop);
    font-family: "Open Sans", Arial, sans-serif;
    position: relative;
  }
  .card {
    position: absolute;
    left: 193px;
    width: 719px;
    height: 410px;
    overflow: hidden;
  }
  .card--front { top: 167px; background: var(--card-white); }
  .card--back  { top: 623px; background: var(--navy); }

  .sun-panel {
    position: absolute;
    inset: 0;
  }

  .brand-vertical {
    position: absolute;
    left: 120px;
    top: 206px;
    transform: translate(-50%, -50%) rotate(-90deg);
    white-space: nowrap;
    color: var(--navy);
    font-weight: 700;
    font-size: 27px;
    letter-spacing: -0.3px;
  }

  .contact {
    position: absolute;
    left: 401px;
    top: 92px;
    color: var(--ink-light);
  }
  .contact__name {
    font-weight: 700;
    font-size: 25px;
    line-height: 32px;
  }
  .contact__role {
    font-size: 19px;
    line-height: 24px;
  }
  .contact__license {
    margin-top: 38px;
    font-size: 18px;
    line-height: 24px;
  }
  .contact__list {
    list-style: none;
    margin-top: 12px;
  }
  .contact__item {
    display: flex;
    align-items: center;
    font-size: 18px;
    line-height: 27.5px;
  }
  .contact__icon {
    width: 16px;
    height: 16px;
    margin: 0 12px 0 10px;
    flex: none;
  }

  .brand-centered {
    position: absolute;
    left: 0;
    right: 0;
    top: 178px;
    text-align: center;
    color: var(--ink-light);
    font-weight: 700;
    font-size: 40px;
    letter-spacing: -0.5px;
    line-height: 52px;
  }
  .back-web {
    position: absolute;
    left: 0;
    right: 0;
    top: 340px;
    text-align: center;
    color: var(--ink-light);
    font-style: italic;
    font-size: 18px;
    letter-spacing: 6px;
  }
</style>
</head>
<body>

  <section class="card card--front">
    <svg class="sun-panel" width="719" height="410" viewBox="0 0 719 410" role="img" aria-label="Sun with rays illustration">
      <circle cx="519" cy="206" r="200" fill="var(--sun)"/>
      <rect x="519" y="0" width="200" height="410" fill="var(--sun-deep)"/>
    </svg>

    <div class="brand-vertical">Velk Partners Building</div>

    <div class="contact">
      <p class="contact__name">Paul Osterby</p>
      <p class="contact__role">CEO/Founder</p>
      <p class="contact__license">CSLB# 3867140</p>
      <ul class="contact__list">
        <li class="contact__item">
          <svg class="contact__icon" viewBox="0 0 16 16" aria-hidden="true">
            <path fill="#fff" d="M3.6 1.2 6 3.8 4.6 5.8c.9 2 2.4 3.6 4.5 4.6l2-1.4 2.6 2.4-1.4 2.6C7.4 13.8 2.2 8.6 1.1 2.6Z"/>
          </svg>
          (619) 555-0187
        </li>
        <li class="contact__item">
          <svg class="contact__icon" viewBox="0 0 16 16" aria-hidden="true">
            <rect x="1" y="3.5" width="14" height="9.5" fill="#fff"/>
            <path d="M1.5 4 8 9l6.5-5" fill="none" stroke="var(--sun)" stroke-width="1.3"/>
          </svg>
          paul@velkpartners.example
        </li>
        <li class="contact__item">
          <svg class="contact__icon" viewBox="0 0 16 16" aria-hidden="true">
            <circle cx="8" cy="8" r="7" fill="#fff"/>
            <path d="M1 8h14M8 1c-3 3.5-3 10.5 0 14M8 1c3 3.5 3 10.5 0 14" fill="none" stroke="var(--sun)" stroke-width="1.1"/>
          </svg>
          www.velkpartners.example
        </li>
      </ul>
    </div>
  </section>

  <section class="card card--back">
    <div class="brand-centered">Velk Partners Building</div>
    <p class="back-web">www.velkpartners.example</p>
  </section>

</body>
</html>
```